Looking for a modern, Professional business card design

We have a simple business card, but are looking for a more modern, professional look. A sample of the basic card is attached as well as the logo. We would also like to add that we offer:
Struggling with your finances?
- Learn to become debt free
- Discover the power of cash
- Control your money instead of it controlling you
Let us help you achieve a new level of financial freedom!
Also, we would like to have a "SPECIAL OFFER!: FREE 30 minute consultation"
Financial Planning

```html
<!DOCTYPE html>
<html lang="en">
<head>
<meta charset="utf-8">
<title>Liberty Money Coaching – Business Card</title>
<link rel="stylesheet" href="https://fonts.googleapis.com/css2?family=Oswald:wght@500;700&family=Roboto:wght@400;900&family=Roboto+Condensed:wght@500;700&display=swap">
<style>
  :root {
    --backdrop: #232323;
    --paper: #ffffff;
    --ink: #111111;
    --body-grey: #4a4a4a;
    --brand-green: #2ea043;
    --band-black: #050505;
    --light-text: #f4f4f4;
  }
  * { margin: 0; padding: 0; box-sizing: border-box; }
  html, body {
    width: 1200px; height: 987px; overflow: hidden;
    background: var(--backdrop);
    font-family: "Roboto", Arial, sans-serif;
  }
  .card {
    position: absolute; left: 293px; width: 615px; height: 352px;
    background: var(--paper); overflow: hidden;
  }
  .card--front { top: 123px; }
  .card--back { top: 499px; }

  /* Front */
  .brand {
    position: absolute; left: 38px; top: 60px;
    display: flex; align-items: center; gap: 12px;
  }
  .brand__dot { width: 22px; height: 22px; border-radius: 50%; background: var(--brand-green); }
  .brand__name {
    font-family: "Oswald", sans-serif; font-weight: 700;
    font-size: 34px; line-height: 1; color: var(--ink); letter-spacing: 0.5px;
    text-transform: uppercase;
  }
  .person { position: absolute; right: 42px; top: 82px; text-align: right; }
  .person__name {
    font-family: "Oswald", sans-serif; font-weight: 700;
    font-size: 28px; line-height: 1; color: var(--brand-green);
  }
  .person__title {
    margin-top: 8px; font-size: 13px; color: var(--ink); letter-spacing: 0.2px;
  }
  .contact-band {
    position: absolute; left: 0; top: 196px; width: 615px; height: 126px;
    background: var(--band-black);
  }
  .contact-band__accent { position: absolute; right: 0; top: 0; }
  .contact-list { position: absolute; left: 41px; top: 26px; list-style: none; }
  .contact-list li {
    display: flex; align-items: center; gap: 10px;
    height: 24px; font-size: 17px; color: var(--light-text);
  }
  .contact-list svg { width: 16px; height: 16px; flex: none; }

  /* Back */
  .pitch { position: absolute; left: 44px; top: 62px; }
  .pitch__heading {
    font-family: "Roboto Condensed", sans-serif; font-weight: 500;
    font-size: 20px; color: var(--brand-green); text-transform: uppercase;
  }
  .pitch__list { list-style: none; margin-top: 6px; }
  .pitch__list li {
    position: relative; padding-left: 18px; height: 26px; line-height: 26px;
    font-size: 17px; color: var(--body-grey);
  }
  .pitch__list li::before {
    content: ""; position: absolute; left: 2px; top: 11px;
    width: 6px; height: 6px; border-radius: 50%; background: var(--brand-green);
  }
  .pitch__promise {
    margin-top: 8px; font-family: "Roboto Condensed", sans-serif; font-weight: 700;
    font-size: 17px; color: var(--ink);
  }
  .offer__headline {
    margin-top: 14px; font-weight: 900; font-size: 44px; line-height: 1;
    color: var(--brand-green); letter-spacing: 0.5px;
  }
  .offer__detail {
    margin-top: 8px; font-weight: 900; font-size: 21px; line-height: 1;
    color: var(--brand-green); letter-spacing: 0.3px;
  }
  .offer__detail strong { color: var(--ink); }
</style>
</head>
<body>
  <section class="card card--front" aria-label="Business card front">
    <div class="brand">
      <span class="brand__dot"></span>
      <span class="brand__name">Liberty Money<br>Coaching</span>
    </div>
    <div class="person">
      <p class="person__name">DANIEL R. HOLLIS</p>
      <p class="person__title">PERSONAL FINANCIAL COACH</p>
    </div>
    <div class="contact-band">
      <svg class="contact-band__accent" width="215" height="126" viewBox="0 0 215 126" aria-hidden="true">
        <path d="M150 0 H215 V126 H50 C90 90 120 40 150 0 Z" fill="var(--brand-green)"/>
      </svg>
      <ul class="contact-list">
        <li>
          <svg viewBox="0 0 16 16" aria-hidden="true"><rect x="4" y="1" width="8" height="14" rx="1.5" fill="none" stroke="var(--brand-green)" stroke-width="1.8"/><rect x="6" y="3" width="4" height="8" fill="var(--brand-green)"/></svg>
          (555) 014-2298
        </li>
        <li>
          <svg viewBox="0 0 16 16" aria-hidden="true"><rect x="1" y="3.5" width="14" height="9" fill="var(--brand-green)"/><path d="M1 3.5 L8 9 L15 3.5" fill="none" stroke="var(--band-black)" stroke-width="1.2"/></svg>
          daniel@steadymoneypath.com
        </li>
        <li>
          <svg viewBox="0 0 16 16" aria-hidden="true"><circle cx="8" cy="8" r="7" fill="var(--brand-green)"/><path d="M1 8 H15 M8 1 C4 5 4 11 8 15 M8 1 C12 5 12 11 8 15" fill="none" stroke="var(--band-black)" stroke-width="1"/></svg>
          www.steadymoneypath.com
        </li>
      </ul>
    </div>
  </section>

  <section class="card card--back" aria-label="Business card back">
    <div class="pitch">
      <h2 class="pitch__heading">Struggling with your finances?</h2>
      <ul class="pitch__list">
        <li>Learn to become debt free</li>
        <li>Discover the power of cash</li>
        <li>Control your money instead of it controlling you</li>
      </ul>
      <p class="pitch__promise">Let us help you achieve a new level of financial freedom!</p>
      <p class="offer__headline">SPECIAL OFFER!</p>
      <p class="offer__detail"><strong>FREE</strong> 30 MINUTE CONSULTATION</p>
    </div>
  </section>
</body>
</html>
```